Income Tax Flyer - Updates Needed

Just need to update this flyer design and give it a new look. We would like to keep all the same wording but make it stand out a little more. Our selling point is the "Same Day Tax Advance up to $6,000"

Lending, Small Loans, Tax Services, Title Loans, Personal Loans

```html
<!DOCTYPE html>
<html lang="en">
<head>
<meta charset="utf-8">
<title>Same Day Tax Advance Flyer</title>
<link href="https://fonts.googleapis.com/css2?family=Oswald:wght@600;700&family=Poppins:wght@400;500;600;700&display=swap" rel="stylesheet">
<style>
:root{
  --bg:#e6e6e6;
  --paper:#ffffff;
  --red:#c93a34;
  --red-deep:#a92d2a;
  --green:#1f5a32;
  --green-dark:#174527;
  --gold:#e6b84a;
  --ink:#3a3d3f;
  --charcoal:#2e3436;
  --money-light:#dfe3d6;
  --money-mid:#b9c4ad;
}
*{margin:0;padding:0;box-sizing:border-box}
html,body{width:1200px;height:2400px;overflow:hidden;background:var(--bg)}
.flyer{
  position:absolute;left:50px;top:354px;width:800px;height:1230px;
  transform:scale(1.375);transform-origin:top left;
  background:var(--paper);overflow:hidden;
  box-shadow:0 10px 30px rgba(0,0,0,.25);
  font-family:'Poppins',sans-serif;
}
.bills-top{position:absolute;left:0;top:0;width:800px;height:470px;
  background:radial-gradient(ellipse at 50% 0%,rgba(185,196,173,.55),rgba(255,255,255,0) 70%)}
.band{position:absolute;left:0;top:0;width:800px;height:1230px}
.money-stack{position:absolute;left:625px;top:500px;width:175px;height:165px;
  background:linear-gradient(160deg,var(--money-light),var(--money-mid));border-radius:10px;transform:rotate(-8deg)}
.brand{position:absolute;left:0;top:150px;width:800px;display:flex;justify-content:center;align-items:center;gap:12px}
.brand-dot{width:20px;height:20px;border-radius:50%;background:var(--red)}
.brand-name{font-size:36px;font-weight:600;color:var(--green);letter-spacing:.5px}
.headline{position:absolute;left:196px;top:238px;transform:rotate(-4deg);transform-origin:left top;
  font-family:'Oswald',sans-serif;font-weight:700;line-height:.82;text-transform:uppercase}
.headline span{display:block;transform-origin:left center;white-space:nowrap}
.headline .same-day{font-size:112px;color:var(--red);transform:scaleX(.84)}
.headline .tax-advance{font-size:100px;color:var(--charcoal);transform:scaleX(.71)}
.amount{position:absolute;left:168px;top:398px;transform:rotate(-4deg) scaleX(.76);transform-origin:left top;white-space:nowrap;
  font-family:'Oswald',sans-serif;font-weight:700;font-size:205px;line-height:1;color:var(--green);letter-spacing:-3px;
  text-shadow:3px 3px 0 #fff,-3px -3px 0 #fff,3px -3px 0 #fff,-3px 3px 0 #fff,8px 6px 0 var(--green-dark),10px 8px 0 var(--green-dark)}
.up-to{position:absolute;left:363px;top:413px;width:52px;height:52px;border-radius:50%;background:var(--gold);
  color:var(--green);font-weight:700;font-size:15px;line-height:14px;display:flex;align-items:center;justify-content:center;text-align:center;z-index:2}
.tagline{position:absolute;left:0;top:645px;width:770px;text-align:center;color:#fff;font-weight:700;font-size:43px;line-height:48px}
.features{position:absolute;left:0;top:780px;width:800px;height:230px}
.feature{position:absolute;top:0;width:240px;text-align:center}
.feature-1{left:43px}.feature-2{left:283px}.feature-3{left:527px}
.badge{width:124px;height:124px;border-radius:50%;background:#fff;margin:0 auto;display:flex;align-items:center;justify-content:center}
.badge-inner{width:100px;height:100px;border-radius:50%;background:var(--green);display:flex;align-items:center;justify-content:center}
.feature-label{margin-top:22px;font-size:24px;font-weight:600;color:var(--ink);line-height:28px}
.divider{position:absolute;top:890px;height:110px;border-left:2px dashed #9a9a9a}
.contact-bar{position:absolute;left:50px;top:1033px;width:708px;height:40px}
.contact-label{position:absolute;left:0;top:0;width:320px;height:40px;background:var(--red);border-radius:20px 0 0 20px;
  color:#fff;font-weight:600;font-size:22px;line-height:40px;padding-left:28px}
.contact-phone{position:absolute;left:310px;top:0;width:398px;height:40px;background:var(--green);border-radius:20px;
  color:#fff;font-weight:700;font-size:34px;line-height:42px;padding-left:46px;letter-spacing:3px}
.phone-icon{position:absolute;left:296px;top:4px;width:32px;height:32px;border-radius:50%;background:var(--gold);display:flex;align-items:center;justify-content:center}
.locations{position:absolute;left:0;top:1095px;width:800px}
.location{position:absolute;top:0;width:215px;font-size:15px;line-height:19px;color:var(--ink);white-space:nowrap}
.location strong{font-weight:600;display:block;margin-top:4px}
.loc-1{left:52px}.loc-2{left:286px}.loc-3{left:523px}
.loc-divider{position:absolute;top:1100px;height:90px;border-left:1px solid #bbb}
</style>
</head>
<body>
<div class="flyer">
  <div class="bills-top" role="img" aria-label="Falling dollar bills across the top of the flyer"></div>

  <svg class="band" viewBox="0 0 800 1230" aria-hidden="true">
    <polygon fill="var(--red)" points="0,600 120,585 240,570 360,555 480,538 600,515 700,495 800,478 800,800 700,815 600,835 520,845 480,850 400,862 300,880 200,895 100,905 0,922"/>
    <polygon fill="var(--red-deep)" opacity=".35" points="0,760 800,640 800,800 0,922"/>
  </svg>

  <div class="money-stack" role="img" aria-label="Stacks of banded hundred-dollar bills"></div>

  <div class="brand">
    <span class="brand-dot"></span>
    <span class="brand-name">Quillbrook Lending Co.</span>
  </div>

  <h1 class="headline"><span class="same-day">Same Day</span><span class="tax-advance">Tax Advance</span></h1>
  <div class="amount">$6,000</div>
  <div class="up-to">UP<br>TO</div>

  <p class="tagline">File Your Taxes and<br>Apply for an EASY ADVANCE!</p>

  <div class="features">
    <div class="feature feature-1">
      <div class="badge"><div class="badge-inner">
        <svg width="64" height="64" viewBox="0 0 64 64"><circle cx="32" cy="32" r="26" fill="none" stroke="var(--gold)" stroke-width="3"/><line x1="32" y1="24" x2="32" y2="10" stroke="var(--gold)" stroke-width="3"/><text x="32" y="44" text-anchor="middle" font-family="Poppins,sans-serif" font-weight="700" font-size="22" fill="var(--gold)">24</text></svg>
      </div></div>
      <p class="feature-label">Available<br>in 24 Hours<br>or Less</p>
    </div>
    <div class="feature feature-2">
      <div class="badge"><div class="badge-inner">
        <svg width="64" height="64" viewBox="0 0 64 64"><circle cx="32" cy="26" r="14" fill="none" stroke="var(--gold)" stroke-width="3"/><text x="32" y="33" text-anchor="middle" font-family="Poppins,sans-serif" font-weight="700" font-size="20" fill="var(--gold)">$</text><path d="M8 50 h14 l10 4 h18 l6 -6" fill="none" stroke="var(--gold)" stroke-width="3" stroke-linejoin="round"/></svg>
      </div></div>
      <p class="feature-label">Choose<br>Your Loan<br>Amount</p>
    </div>
    <div class="feature feature-3">
      <div class="badge"><div class="badge-inner">
        <svg width="64" height="64" viewBox="0 0 64 64"><rect x="22" y="8" width="24" height="46" rx="4" fill="var(--gold)"/><rect x="26" y="14" width="16" height="10" fill="var(--green)"/><rect x="12" y="34" width="14" height="16" rx="3" fill="var(--gold)" stroke="var(--green)" stroke-width="2"/></svg>
      </div></div>
      <p class="feature-label">Quick and<br>Easy</p>
    </div>
  </div>
  <div class="divider" style="left:285px"></div>
  <div class="divider" style="left:522px"></div>

  <div class="contact-bar">
    <div class="contact-label">CONTACT US TODAY!</div>
    <div class="contact-phone">+1 555 014 2290</div>
    <div class="phone-icon"><svg width="18" height="18" viewBox="0 0 24 24"><path d="M6.6 10.8a15 15 0 0 0 6.6 6.6l2.2-2.2c.3-.3.7-.4 1-.2 1.1.4 2.3.6 3.6.6.6 0 1 .4 1 1V20c0 .6-.4 1-1 1A17 17 0 0 1 3 4c0-.6.4-1 1-1h3.5c.6 0 1 .4 1 1 0 1.3.2 2.5.6 3.6.1.3 0 .7-.2 1z" fill="#fff"/></svg></div>
  </div>

  <div class="locations">
    <div class="location loc-1">
      <svg width="16" height="22" viewBox="0 0 16 22"><path d="M8 0a8 8 0 0 0-8 8c0 6 8 14 8 14s8-8 8-14a8 8 0 0 0-8-8z" fill="#e0202a"/><circle cx="8" cy="8" r="3" fill="#fff"/></svg>
      <strong>Marlow Bend – Hillcrest</strong>2218 Maple Ridge Ave<br>Marlow Bend, TX 70911
    </div>
    <div class="location loc-2">
      <svg width="16" height="22" viewBox="0 0 16 22"><path d="M8 0a8 8 0 0 0-8 8c0 6 8 14 8 14s8-8 8-14a8 8 0 0 0-8-8z" fill="#e0202a"/><circle cx="8" cy="8" r="3" fill="#fff"/></svg>
      <strong>Fernvale</strong>880 Cedar Hollow Rd #210<br>Fernvale, TX 70922
    </div>
    <div class="location loc-3">
      <svg width="16" height="22" viewBox="0 0 16 22"><path d="M8 0a8 8 0 0 0-8 8c0 6 8 14 8 14s8-8 8-14a8 8 0 0 0-8-8z" fill="#e0202a"/><circle cx="8" cy="8" r="3" fill="#fff"/></svg>
      <strong>Orin Falls – Northgate</strong>4520 Bluebonnet Blvd, Ste. 5<br>Orin Falls, TX 70933
    </div>
  </div>
  <div class="loc-divider" style="left:268px"></div>
  <div class="loc-divider" style="left:506px"></div>
</div>
</body>
</html>
```